Brimsett Gardening Fresh New Website

We are looking to create a simple fresh website for our landscaping business. The website should appeal to a 'high end' audience. We deal with a lot of Embassies and affluent clients who have extremely large gardens that are meticulously maintained. The site is about communicating our excellent landscaping and customer service skills and encouraging new clients to reach out and engage us to take care of their gardens.

The website is basically going to be our business card, it will have almost no functionality other than two 'contact us' forms, one for smaller clients and one for more detailed projects.

The website will not have a lot of written content and will have to show photos of beautifully landscaped gardens.

The main logo in black will influence the site, however, we are open to all suggestions.

We are expecting to have the following pages:
Home Page
Services
About Us
Contact Us
Showcase (photo gallery of our work)

We need someone who can code it to wordpress and be available for minor changes over a number of days. They will be simple tweaks.

```html
<!DOCTYPE html>
<html lang="en">
<head>
<meta charset="utf-8">
<title>Brimsett Gardening</title>
<link rel="stylesheet" href="https://fonts.googleapis.com/css2?family=Cinzel:wght@400;600;700&family=Cormorant+Garamond:wght@500;600&family=Lato:wght@400;700&display=swap">
<style>
:root{
  --black:#000;
  --gold:#c49a3a;
  --gold-dark:#a9781f;
  --gold-grad:linear-gradient(90deg,#a9781f,#e7c258 60%,#f3d873);
  --white:#fff;
  --text:#333;
  --muted:#666;
  --light:#f7f7f7;
  --cream:#fdf8ec;
  --lawn:linear-gradient(160deg,#6fa63a,#3f7a22 60%,#2b5a17);
}
*{box-sizing:border-box;margin:0;padding:0}
html,body{width:1200px;height:4785px;overflow:hidden}
body{font-family:'Lato',sans-serif;color:var(--text);background:var(--white);position:relative}
.abs{position:absolute}
.photo{position:absolute}
/* header */
.site-header{position:absolute;left:0;top:0;width:1200px;height:141px;background:var(--black);z-index:3}
.brand{position:absolute;left:92px;top:0;width:208px;height:224px;background:var(--black);border-radius:0 0 104px 104px;z-index:4;text-align:center;color:var(--gold)}
.brand-dot{width:34px;height:34px;border-radius:50%;border:2px solid var(--gold);margin:34px auto 22px}
.brand-name{font-family:'Cinzel',serif;font-size:24px;letter-spacing:5px;line-height:1}
.brand-sub{font-family:'Cinzel',serif;font-size:13px;letter-spacing:7px;margin-top:8px}
.top-contact{position:absolute;top:16px;right:112px;display:flex;gap:34px;color:var(--white);font-family:'Cormorant Garamond',serif;font-weight:600;font-size:16px;align-items:center}
.top-contact span{display:flex;align-items:center;gap:12px}
.icon-ring{width:30px;height:30px;border-radius:50%;border:2px solid var(--gold);display:flex;align-items:center;justify-content:center}
.nav{position:absolute;top:82px;left:418px;display:flex;align-items:center;font-family:'Cinzel',serif;font-size:13px;color:var(--white)}
.nav a{color:inherit;text-decoration:none;margin-right:38px}
.btn{display:inline-flex;align-items:center;justify-content:center;background:var(--gold-grad);color:#2a1a00;font-family:'Cinzel',serif;font-weight:700;font-size:13px;border-radius:4px;box-shadow:0 4px 8px rgba(0,0,0,.25)}
.nav .btn{width:130px;height:38px}
/* hero */
.hero{position:absolute;left:0;top:141px;width:1200px;height:535px;background:linear-gradient(170deg,#4d7f24,#6fa83a 40%,#3c6b1c)}
.hero h1{position:absolute;top:308px;width:100%;text-align:center;color:var(--white);font-family:'Cinzel',serif;font-weight:600;font-size:38px;letter-spacing:1px}
.hero-form{position:absolute;top:399px;left:135px;display:flex;gap:12px}
.field{width:181px;height:48px;border:2px solid var(--white);color:var(--white);font-size:14px;padding:0 16px;display:flex;align-items:center;justify-content:space-between}
.hero-form .btn{width:146px;height:48px;margin-left:6px;font-size:14px}
.dots{position:absolute;top:491px;left:0;width:100%;display:flex;justify-content:center;gap:8px}
.dots i{width:8px;height:8px;border-radius:50%;background:rgba(255,255,255,.75)}
.dots i.on{background:var(--white);transform:scale(1.2)}
/* tiles */
.tile{position:absolute;top:683px;height:348px;width:292px}
.tile span{position:absolute;bottom:28px;width:100%;text-align:center;color:var(--white);font-family:'Cinzel',serif;font-size:18px;font-weight:600}
/* section titles */
.ornament{position:absolute;left:584px;width:32px;height:32px;border-radius:50%;border:2px solid var(--gold)}
.sec-title{position:absolute;width:100%;text-align:center;font-family:'Cinzel',serif;font-size:35px;color:var(--gold);letter-spacing:1px}
/* intro */
.intro{position:absolute;top:1040px;left:0;width:1200px;height:523px;background:var(--light)}
.card{position:absolute;top:195px;width:309px;height:247px;background:var(--white);box-shadow:0 2px 10px rgba(0,0,0,.07);text-align:center;padding:0 18px}
.card .ornament{position:relative;left:auto;margin:34px auto 0}
.card h3{font-family:'Cinzel',serif;font-size:15px;color:#111;margin-top:32px;letter-spacing:.5px}
.card p{font-size:12px;line-height:24px;color:var(--muted);margin-top:12px}
/* about */
.about-title{position:absolute;left:108px;top:1713px;font-family:'Cinzel',serif;font-size:35px;color:var(--gold)}
.about-sub{position:absolute;left:110px;top:1772px;font-family:'Cinzel',serif;font-size:17px;letter-spacing:6px;color:var(--gold-dark)}
.about-text{position:absolute;left:111px;top:1816px;width:440px;font-size:14px;line-height:29px;color:#444}
/* listing */
.listing{position:absolute;top:2343px;width:371px;height:324px;background:var(--white);box-shadow:0 2px 10px rgba(0,0,0,.12);text-align:center}
.listing .photo{position:relative;height:238px;width:100%}
.listing h4{font-weight:400;font-size:17px;color:#222;margin-top:16px}
.listing p{font-size:14px;color:var(--muted);margin-top:12px}
/* testimonial */
.testi{position:absolute;top:2838px;left:0;width:1200px;height:661px;background:var(--cream)}
.avatar{position:absolute;border-radius:50%}
.quote{position:absolute;font-family:Georgia,serif;font-size:220px;color:#e2ded5;line-height:1}
/* portfolio */
.pf{position:absolute;height:275px}
/* footer */
.site-footer{position:absolute;top:4350px;left:0;width:1200px;height:435px;background:#050505;color:var(--white)}
.site-footer h5{position:absolute;top:78px;font-family:'Cinzel',serif;font-size:14px;font-weight:700}
.links{position:absolute;left:111px;top:119px;list-style:none;font-size:12px}
.links li{height:33px}
.links li::before{content:"»";margin-right:14px;color:#ddd}
.contact-row{position:absolute;left:293px;display:flex;align-items:center;gap:20px;font-size:12px;line-height:17px}
.ff{position:absolute;background:var(--white);color:#888;font-size:11px;padding:9px 12px;height:33px}
.social{position:absolute;top:4708px;display:flex;gap:10px;left:944px}
.social i{width:30px;height:30px;border-radius:50%;border:1.5px solid var(--white)}
.social i.on{background:var(--gold)}
</style>
</head>
<body>

<header class="site-header">
  <div class="top-contact">
    <span><span class="icon-ring"><svg width="14" height="14" viewBox="0 0 24 24"><path d="M6 2l4 4-2 3a12 12 0 0 0 7 7l3-2 4 4-3 4C10 22 2 14 2 5z" fill="#c49a3a"/></svg></span>+1 555 014 2270</span>
    <span><span class="icon-ring"><svg width="14" height="14" viewBox="0 0 24 24"><rect x="2" y="5" width="20" height="14" fill="none" stroke="#c49a3a" stroke-width="2"/><path d="M2 6l10 7 10-7" fill="none" stroke="#c49a3a" stroke-width="2"/></svg></span>info@brimsettgardening.com</span>
  </div>
  <nav class="nav">
    <a>HOME</a><a>SERVICES</a><a>ABOUT US</a><a>CONTACT US</a><a>SHOWCASE</a>
    <span class="btn">CONTACT US</span>
  </nav>
</header>
<div class="brand">
  <div class="brand-dot"></div>
  <div class="brand-name">BRIMSETT</div>
  <div class="brand-sub">GARDENING</div>
</div>

<section class="hero" role="img" aria-label="Aerial view of a gardener mowing a striped lawn with a yellow mower">
  <h1>WELCOME TO BRIMSETT GARDENING</h1>
  <div class="hero-form">
    <div class="field">Name</div>
    <div class="field">Email</div>
    <div class="field">Phone Number</div>
    <div class="field">Location <span>&#8693;</span></div>
    <span class="btn">SUBMIT</span>
  </div>
  <div class="dots"><i></i><i></i><i class="on"></i><i></i></div>
</section>

<div class="tile" style="left:5px;background:linear-gradient(170deg,#4d6a3a,#4f8a2b 60%,#7a7a70)" role="img" aria-label="Paved path curving past hostas and stone steps"><span>TEMPORIBUS AUTEM</span></div>
<div class="tile" style="left:304px;background:linear-gradient(180deg,#9cc6ec,#7fb04b 55%,#4f8a2b)" role="img" aria-label="Lawn with fence, tree and patio under blue sky"><span>ITAQUE EARUM RERUM</span></div>
<div class="tile" style="left:603px;background:linear-gradient(180deg,#b8a25a,#5c7a33 50%,#2f4a1f)" role="img" aria-label="Rose arch tunnel over a garden path"><span>REICIENDIS VOLUPT</span></div>
<div class="tile" style="left:902px;background:linear-gradient(170deg,#6b5a3a,#4e6b2f 50%,#3e5a24)" role="img" aria-label="Garden seating area with blue armchairs and flowers"><span>ALIAS CONSEQUATUR</span></div>

<section class="intro">
  <div class="ornament" style="top:54px"></div>
  <h2 class="sec-title" style="top:122px">BRIMSETT GARDENING</h2>
  <div class="card" style="left:111px"><div class="ornament"></div><h3>LOCALLY OWNED &amp; OPERATED</h3><p>Temporibus autem quibusdam et aut officiis debitis aut rerum necessitatibus saepe eveniet ut et volupe non recusandae.</p></div>
  <div class="card" style="left:446px"><div class="ornament"></div><h3>24/7 GUEST &amp; OWNER SERVICES</h3><p>Itaque earum rerum hic tenetur a sapiente delectus, ut aut reiciendis voluptatibus maiores dis doloribus asperiores repellat.</p></div>
  <div class="card" style="left:778px"><div class="ornament"></div><h3>ITAQUE EARUM RERUM</h3><p>Itaque earum rerum hic tenetur a sapiente delectus, ut aut reiciendis voluptatibus maiores dis doloribus asperiores repellat.</p></div>
</section>

<div class="ornament" style="left:111px;top:1648px"></div>
<h2 class="about-title">ABOUT BRIMSETT</h2>
<div class="about-sub">GARDENING</div>
<p class="about-text">Nam libero tempore, cum soluta nobis est eligendi optio cumque uptas assumenda est, poribus autem quibusdam et aut officiis voluptates repudiandae sint et molestiae non recusandae. Itaque earum rerum hic tenetur a sapiente delectus, ut aut reiciendis as rferendis doloribus asperiores repellat.</p>
<span class="btn abs" style="left:111px;top:1980px;width:134px;height:42px">READ MORE</span>
<div class="photo" style="left:600px;top:1563px;width:600px;height:532px;background:var(--lawn)" role="img" aria-label="Landscaper kneeling to lay rolls of fresh turf beside a wheelbarrow"></div>

<div class="ornament" style="top:2197px"></div>
<h2 class="sec-title" style="top:2264px">GARDENING LISTING</h2>
<div class="listing" style="left:26px"><div class="photo" style="background:linear-gradient(180deg,#8ec0ea,#a68a6a 45%,#5f8f35)" role="img" aria-label="Suburban house with landscaped front garden"></div><h4>Temporibus autem quibusdam</h4><p>Blanditiis praesentium</p></div>
<div class="listing" style="left:416px"><div class="photo" style="background:linear-gradient(180deg,#8a5a3a,#b8b04a 30%,#5f9a30 60%,#6aa535)" role="img" aria-label="Flower borders beside a brick wall and lawn"></div><h4>Itaque earum rerum</h4><p>Voluptatum deleniti atque</p></div>
<div class="listing" style="left:804px"><div class="photo" style="background:linear-gradient(170deg,#3f6a24,#5a8a33 60%,#8a9aa8)" role="img" aria-label="Gardener trimming a hedge with shears"></div><h4>Reiciendis voluptatibus maiores</h4><p>Corrupti quos dolores</p></div>
<span class="btn abs" style="left:534px;top:2722px;width:134px;height:42px">VIEW MORE</span>

<section class="testi">
  <div class="ornament" style="top:52px"></div>
  <h2 class="sec-title" style="top:122px">WHAT CUSTOMER SAYS</h2>
  <div class="avatar" style="left:540px;top:189px;width:140px;height:140px;border:3px solid var(--gold);background:#c9b8a4" role="img" aria-label="Portrait of the customer"></div>
  <div class="avatar" style="left:138px;top:283px;width:66px;height:66px;background:#d9b9a2" role="img" aria-label="Portrait of another customer"></div>
  <div class="avatar" style="left:1017px;top:206px;width:46px;height:46px;background:#b8a598" role="img" aria-label="Portrait of another customer"></div>
  <div class="avatar" style="left:382px;top:316px;width:13px;height:13px;background:#f2c230"></div>
  <div class="avatar" style="left:898px;top:283px;width:6px;height:6px;background:#c49a3a"></div>
  <div class="quote" style="left:160px;top:335px">&ldquo;</div>
  <div class="quote" style="left:955px;top:420px">&rdquo;</div>
  <div class="abs" style="top:352px;width:100%;text-align:center;font-size:21px;font-weight:700;color:#111">Dorian Vellmont</div>
  <div class="abs" style="top:389px;left:540px;width:140px;text-align:center;font-size:11px;font-weight:700;color:#777">United States</div>
  <div class="abs" style="top:414px;left:0;width:1221px;text-align:center;font-size:30px;color:#f2b820;letter-spacing:1px">&#9733;&#9733;&#9733;&#9733;&#9733;</div>
  <p class="abs" style="top:465px;left:282px;width:656px;text-align:center;font-size:14px;line-height:29px;color:#333">Itaque earum rerum hic tenetur a sapiente delectus, ut aut reiciendis voluptatibus maiores alias. Consequatur aut perferendis doloribus asperiores repellat.Et harum quidem rerum facilis est et expedita distinctio.</p>
  <div class="abs" style="top:576px;left:0;width:100%;display:flex;justify-content:center;gap:7px">
    <i style="width:13px;height:13px;border-radius:50%;background:#d6d9ec"></i><i style="width:13px;height:13px;border-radius:50%;background:#d6d9ec"></i><i style="width:13px;height:13px;border-radius:50%;background:#d6d9ec"></i><i style="width:13px;height:13px;border-radius:50%;background:#b8862b"></i><i style="width:13px;height:13px;border-radius:50%;background:#d6d9ec"></i><i style="width:13px;height:13px;border-radius:50%;background:#d6d9ec"></i>
  </div>
</section>

<div class="ornament" style="top:3566px"></div>
<h2 class="sec-title" style="top:3634px">OUR PORTFOLIO</h2>
<div class="pf" style="top:3710px;left:13px;width:279px;background:linear-gradient(160deg,#8a8a7a,#5f7a45 50%,#d8d8d0)" role="img" aria-label="Gardeners holding a tray of flower seedlings"></div>
<div class="pf" style="top:3710px;left:303px;width:278px;background:linear-gradient(160deg,#2f5a1f,#5a8a30 50%,#d86a2a)" role="img" aria-label="Hedge trimmer cutting a green hedge"></div>
<div class="pf" style="top:3710px;left:591px;width:293px;background:linear-gradient(170deg,#7aa04a,#4a6a2a 55%,#5a4030)" role="img" aria-label="Gloved hands planting a seedling in soil"></div>
<div class="pf" style="top:3710px;left:895px;width:293px;background:linear-gradient(170deg,#6a7a4a,#4a3a2a 55%,#d9d9d9)" role="img" aria-label="Planting white flowers with a trowel"></div>
<div class="pf" style="top:3996px;left:13px;width:371px;background:linear-gradient(170deg,#9ab070,#5f8a35 50%,#b8a890)" role="img" aria-label="Raised wooden vegetable beds on gravel"></div>
<div class="pf" style="top:3996px;left:396px;width:390px;background:linear-gradient(170deg,#3f6a24,#c8506a 45%,#5f9a30)" role="img" aria-label="Curving flower border beside a lawn"></div>
<div class="pf" style="top:3996px;left:798px;width:390px;background:linear-gradient(170deg,#f0d070,#7aa83a 45%,#3f7a22)" role="img" aria-label="Lawn mower on grass in golden sunlight"></div>

<footer class="site-footer">
  <h5 style="left:111px">QUICK LINKS</h5>
  <h5 style="left:293px">CONTACT INFORMATION</h5>
  <h5 style="left:637px">GET IN TOUCH:</h5>
  <ul class="links"><li>Home</li><li>About</li><li>Services</li><li>Gallery</li><li>Contact</li></ul>
  <div class="contact-row" style="top:125px"><span class="icon-ring" style="width:34px;height:34px;border-color:#ddd"><svg width="14" height="14" viewBox="0 0 24 24"><path d="M12 2a7 7 0 0 0-7 7c0 5 7 13 7 13s7-8 7-13a7 7 0 0 0-7-7zm0 10a3 3 0 1 1 0-6 3 3 0 0 1 0 6z" fill="#c49a3a"/></svg></span><span>Brimsett Gardening<br>Northvale &amp; Eastmoor</span></div>
  <div class="contact-row" style="top:172px"><span class="icon-ring" style="width:34px;height:34px;border-color:#ddd"><svg width="14" height="14" viewBox="0 0 24 24"><path d="M6 2l4 4-2 3a12 12 0 0 0 7 7l3-2 4 4-3 4C10 22 2 14 2 5z" fill="#c49a3a"/></svg></span><span>Phone : +1 555 014 2270</span></div>
  <div class="contact-row" style="top:218px"><span class="icon-ring" style="width:34px;height:34px;border-color:#ddd"><svg width="14" height="14" viewBox="0 0 24 24"><rect x="2" y="5" width="20" height="14" fill="none" stroke="#c49a3a" stroke-width="2"/><path d="M2 6l10 7 10-7" fill="none" stroke="#c49a3a" stroke-width="2"/></svg></span><span>Email : info@brimsettgardening.com</span></div>
  <div class="ff" style="left:637px;top:116px;width:221px">Name :</div>
  <div class="ff" style="left:867px;top:116px;width:219px">Phone :</div>
  <div class="ff" style="left:637px;top:160px;width:449px">Email :</div>
  <div class="ff" style="left:637px;top:201px;width:449px;height:72px">Message :</div>
  <span class="btn abs" style="left:1006px;top:287px;width:80px;height:32px;font-size:12px">SUBMIT</span>
  <div class="abs" style="left:111px;top:348px;width:989px;height:1px;background:#333"></div>
  <div class="abs" style="left:111px;top:372px;font-size:11px">Copyright © 2024.Brimsett. All Rights Reserved. &nbsp;|&nbsp; Privacy policy</div>
</footer>
<div class="social"><i></i><i class="on"></i><i></i><i></i></div>

</body>
</html>
```